New letter head for Air Conditioning business

We need a new professional letter head design to suit our new re-branded air conditioning business. Our new logo is attached

```html
<!DOCTYPE html>
<html lang="en">
<head>
<meta charset="utf-8">
<title>Norvale Letterhead</title>
<link href="https://fonts.googleapis.com/css2?family=Open+Sans:wght@400;600&family=Lato:wght@400;700&display=swap" rel="stylesheet">
<style>
  :root {
    --paper: #ffffff;
    --ink: #3a3a3a;
    --ink-soft: #4a4a4a;
    --brand-dark: #3d3d3f;
    --brand-green: #66c28a;
    --brand-red: #ef6b5e;
    --footer-text: #ffffff;
  }
  html, body {
    margin: 0;
    padding: 0;
    width: 1040px;
    height: 1200px;
    overflow: hidden;
    background: var(--paper);
  }
  .letterhead {
    position: relative;
    width: 1040px;
    height: 1200px;
    background: var(--paper);
    font-family: "Open Sans", Arial, sans-serif;
    color: var(--ink);
  }
  .brand {
    position: absolute;
    top: 38px;
    left: 0;
    width: 1040px;
    display: flex;
    justify-content: center;
    align-items: center;
    gap: 14px;
  }
  .brand-dot {
    width: 34px;
    height: 34px;
    border-radius: 50%;
    background: var(--brand-green);
  }
  .brand-name {
    font-family: "Open Sans", Arial, sans-serif;
    font-weight: 600;
    font-size: 40px;
    letter-spacing: 6px;
    color: var(--brand-dark);
    line-height: 1;
  }
  .letter-body {
    position: absolute;
    left: 98px;
    width: 844px;
    font-size: 15.5px;
    color: var(--ink-soft);
  }
  .issue-date { position: absolute; top: 222px; left: 98px; font-size: 15.5px; }
  .recipient {
    position: absolute;
    top: 258px;
    left: 98px;
    font-size: 15.5px;
    line-height: 18px;
    margin: 0;
  }
  .salutation { position: absolute; top: 362px; left: 98px; font-size: 15.5px; }
  .paragraph {
    position: absolute;
    left: 98px;
    width: 844px;
    margin: 0;
    font-size: 15.5px;
    line-height: 27px;
    text-align: justify;
    color: var(--ink-soft);
  }
  .p1 { top: 414px; }
  .p2 { top: 576px; }
  .p3 { top: 683px; }
  .closing { position: absolute; top: 820px; left: 98px; font-size: 15.5px; }
  .signature {
    position: absolute;
    top: 860px;
    left: 98px;
    width: 220px;
    height: 26px;
    background: linear-gradient(90deg, #e9e9e9, #f6f6f6);
    border-radius: 4px;
  }
  .signer-name {
    position: absolute;
    top: 898px;
    left: 98px;
    font-size: 19px;
    font-weight: 600;
    color: var(--ink);
  }
  .signer-title { position: absolute; top: 930px; left: 98px; font-size: 15.5px; }
  .footer-band {
    position: absolute;
    left: 0;
    bottom: 0;
    width: 1040px;
    height: 82px;
  }
  .stripes-green {
    position: absolute;
    left: 0; top: 0;
    width: 188px; height: 82px;
    background: repeating-linear-gradient(90deg, var(--brand-green) 0 22px, var(--paper) 22px 32px);
  }
  .contact-bar {
    position: absolute;
    left: 188px; top: 0;
    width: 664px; height: 82px;
    background: var(--brand-dark);
    color: var(--footer-text);
    font-family: "Lato", Arial, sans-serif;
    font-size: 18px;
    text-align: center;
    display: flex;
    flex-direction: column;
    justify-content: center;
    line-height: 28px;
  }
  .contact-bar b { font-weight: 700; }
  .stripes-red {
    position: absolute;
    left: 852px; top: 0;
    width: 188px; height: 82px;
    background: repeating-linear-gradient(90deg, var(--paper) 0 10px, var(--brand-red) 10px 32px);
  }
</style>
</head>
<body>
<main class="letterhead">
  <header class="brand">
    <span class="brand-dot"></span>
    <span class="brand-name">NORVALE</span>
  </header>

  <div class="issue-date">Issuing Date: May 5, 2018</div>
  <p class="recipient">Name Of Employee Mr. XYZABC<br>Address of Employee<br>Address Line 2 etc..</p>
  <div class="salutation">Dear Mr.XYZABC</div>

  <p class="paragraph p1">Lorem Ipsum has been the industry's standard dummy text ever since the 1500s, when an unknown printer took a galley of type and scrambled it to make a type specimen book. It has survived not only five centuries, but also the leap into electronic typesetting, remaining essentially unchanged. It was popularised in the 1960s with the release of Letraset sheets containing Lorem Ipsum passages, and more recently with desktop publishing software like Aldus PageMaker including versions of Lorem Ipsum.</p>
  <p class="paragraph p2">Lorem Ipsum is simply dummy text of the printing and typesetting industry. Lorem Ipsum has been the industry's standard dummy text ever since the 1500s, when an unknown printer took a galley of type and scrambled it to make a type specimen book.</p>
  <p class="paragraph p3">It has survived not only five centuries, but also the leap into electronic typesetting, remaining essentially unchanged. It was popularised in the 1960s with the release of Letraset sheets containing Lorem IpsumIpsum passages.</p>

  <div class="closing">Yours Sincerely</div>
  <div class="signature" role="img" aria-label="Handwritten signature of Daniel Morrow"></div>
  <div class="signer-name">Daniel Morrow</div>
  <div class="signer-title">Managing Director</div>

  <footer class="footer-band">
    <div class="stripes-green"></div>
    <div class="contact-bar">
      <div>58 Harbour Row, Eastfield, 45210</div>
      <div><b>P:</b> 044-210 987 654 | <b>E:</b> info@norvaleair.com | www.norvaleair.com</div>
    </div>
    <div class="stripes-red"></div>
  </footer>
</main>
</body>
</html>
```